Small Business Consulting Firm Needs Letterhead

We need a letterhead for our company "Brightpath Plus". Our company does outbound calling and mailing to business owner's companies who have taken high interest loans. These loans tend to put these businesses in a big financial bind short term, and we help them find better financial options. We would like the design to match our colors of our logo. Headers and footers would look nice, but we are open. We would want it to include our address, website, phone, and email info. Our address - 2000 E. Lamar Blvd. Suite 600Website - www.safeguardtoday.comEmail - info@safeguardtoday.comPhone - 855-726-1938
Industry/Entity Type
Financial Planning
Look and feel
Each slider illustrates characteristics of the customer's brand and the style your logo design should communicate.

```html
<!DOCTYPE html>
<html lang="en">
<head>
<meta charset="utf-8">
<title>Brightpath Plus Letterhead</title>
<link href="https://fonts.googleapis.com/css2?family=Montserrat:wght@400;500;600&display=swap" rel="stylesheet">
<style>
  :root {
    --backdrop: #e8e8e5;
    --paper: #ffffff;
    --ink: #2b2b2b;
    --green: #5fa63a;
    --green-light: #79bd45;
    --blue: #0a7cc1;
    --blue-dark: #075e95;
  }
  * { margin: 0; padding: 0; box-sizing: border-box; }
  html, body {
    width: 1200px; height: 1200px; overflow: hidden;
    background: var(--backdrop);
    font-family: "Montserrat", sans-serif;
    color: var(--ink);
  }
  .letterhead {
    position: absolute; left: 175px; top: 50px;
    width: 850px; height: 1100px;
    background: var(--paper);
    box-shadow: 0 10px 28px rgba(0,0,0,0.25);
    overflow: hidden;
  }
  .band { position: absolute; display: block; }
  .band--top { right: 0; top: 0; }
  .band--bottom { left: 0; bottom: 0; }
  .brand {
    position: absolute; left: 50px; top: 134px;
    display: flex; align-items: center; gap: 12px;
  }
  .brand__mark { width: 18px; height: 18px; background: var(--green); }
  .brand__name {
    font-size: 25px; font-weight: 400; letter-spacing: 2px;
    text-transform: uppercase; color: var(--ink);
  }
  .contact {
    position: absolute; left: 540px; top: 118px;
    border-left: 1.5px solid var(--ink);
    padding-left: 28px; height: 74px;
    font-size: 15px; letter-spacing: 0.6px; line-height: 1;
  }
  .contact__line { position: absolute; left: 29px; white-space: nowrap; }
  .contact__line svg { width: 12px; height: 12px; margin-right: 6px; vertical-align: -1px; fill: var(--blue); }
  .letter { position: absolute; left: 50px; width: 750px; font-size: 14.5px; letter-spacing: 0.9px; }
  .letter__date { top: 290px; }
  .letter__recipient { top: 348px; line-height: 22.5px; }
  .letter__salutation { top: 505px; }
  .letter__body { top: 537px; line-height: 25px; text-align: justify; }
  .letter__body p { margin-bottom: 9px; }
  .letter__closing { top: 785px; }
  .signatory { position: absolute; left: 50px; top: 846px; }
  .signatory__name { font-size: 16px; font-weight: 500; letter-spacing: 0.8px; }
  .signatory__role { font-size: 14.5px; letter-spacing: 5px; margin-top: 6px; }
  .website {
    position: absolute; left: 50px; top: 1036px;
    font-size: 15px; font-weight: 600; letter-spacing: 0.7px;
  }
</style>
</head>
<body>
  <main class="letterhead">
    <svg class="band band--top" width="424" height="28" viewBox="0 0 424 28" aria-hidden="true">
      <polygon points="0,0 424,0 424,28 26,28" fill="var(--green)"/>
      <polygon points="120,0 424,0 424,24" fill="var(--green-light)"/>
    </svg>

    <div class="brand">
      <span class="brand__mark"></span>
      <span class="brand__name">Brightpath Plus</span>
    </div>

    <address class="contact" style="font-style:normal">
      <span class="contact__line" style="top:5px">4170 W. Corwin Ave.</span>
      <span class="contact__line" style="top:24px">Suite 310</span>
      <span class="contact__line" style="top:47px">
        <svg viewBox="0 0 24 24"><path d="M6.6 10.8a15.2 15.2 0 0 0 6.6 6.6l2.2-2.2a1 1 0 0 1 1-.25 11.4 11.4 0 0 0 3.6.57 1 1 0 0 1 1 1V20a1 1 0 0 1-1 1A17 17 0 0 1 3 4a1 1 0 0 1 1-1h3.5a1 1 0 0 1 1 1c0 1.25.2 2.45.57 3.57a1 1 0 0 1-.25 1z"/></svg>855-726-1938
      </span>
      <span class="contact__line" style="top:69px">
        <svg viewBox="0 0 24 24"><path d="M2 5h20v2l-10 6L2 7z M2 9l10 6 10-6v10H2z"/></svg>info@brightpathplus.com
      </span>
    </address>

    <p class="letter letter__date">Date: 20 November 2018</p>

    <p class="letter letter__recipient">To<br>Fernhollow Supply Ltd.<br>58 Ashgrove Lane, Unit# B<br>Leeds, UK 4410B72</p>

    <p class="letter letter__salutation">Dear Harlow,</p>

    <div class="letter letter__body">
      <p>Lorem Ipsum is simply dummy text of the printing and typesetting industry. Lorem Ipsum has been the industry's standard dummy text ever since the 1500s, when an unknown printer took a galley of type and scrambled it to make a type specimen book. It has survived not only five centuries, but also the leap into electronic typesetting, remaining essentially unchanged. It was popularised in the 1960s with the release of Typeline sheets containing Lorem Ipsum passages, and more recently with desktop publishing software like Pagecraft Studio including versions of Lorem Ipsum.</p>
      <p>Lorem Ipsum is simply dummy text of the printing and typesetting industry. Lorem Ipsum has been the industry's.</p>
    </div>

    <p class="letter letter__closing">Thanking you</p>

    <div class="signatory">
      <p class="signatory__name">Mara Quillon</p>
      <p class="signatory__role">CEO</p>
    </div>

    <p class="website">www.brightpathplus.com</p>

    <svg class="band band--bottom" width="425" height="28" viewBox="0 0 425 28" aria-hidden="true">
      <polygon points="0,0 397,0 425,28 0,28" fill="var(--blue)"/>
      <polygon points="0,0 397,0 410,14" fill="var(--blue-dark)"/>
    </svg>
  </main>
</body>
</html>
```